Company web site

Looking for a full responsive(mobile friendly) wordpress implementation

Some material is in the website -- brelvanto.wordpress.com

But looking for a template more consistent with the logo design, and more future looking.

Target Market(s)

Enterprise Clients

Industry/Entity Type

It Company

Font styles to use
Sans Serif

Colors
33a6d7
0255a3
0455a3
cfdeed
85abd2
3176b5

Requirements
Must have
• about, contact information, partner page, success stories, customer testimonials. links to social presence.
• pricing information

```html
<!DOCTYPE html>
<html lang="en">
<head>
<meta charset="utf-8">
<title>Brelvanto – Bridging connected devices with enterprise solutions</title>
<link href="https://fonts.googleapis.com/css2?family=Raleway:wght@400;500;600;700;800&display=swap" rel="stylesheet">
<style>
:root{
  --sky:#33a6d7;
  --navy:#0255a3;
  --mid:#3176b5;
  --pale:#cfdeed;
  --soft:#85abd2;
  --violet:#6a5cc2;
  --ink:#3d3d3d;
  --grey-bg:#f4f4f4;
  --foot-bg:#ececec;
  --line:#dcdcdc;
  --white:#ffffff;
}
*{box-sizing:border-box;margin:0;padding:0}
html,body{width:1200px;height:3689px;overflow:hidden}
body{font-family:"Raleway",sans-serif;color:var(--ink);background:var(--white);position:relative}
.abs{position:absolute}
/* header */
.site-header{top:0;left:0;width:1200px;height:110px;background:var(--white)}
.brand{left:135px;top:30px;display:flex;align-items:center;gap:12px}
.brand-dot{width:46px;height:46px;border-radius:50%;background:var(--sky)}
.brand-name{font-size:32px;font-weight:700;color:var(--sky)}
.main-nav{left:510px;top:44px;display:flex;gap:31px;font-size:13px;font-weight:500}
.main-nav a{color:var(--ink);text-decoration:none}
.main-nav a.active{color:var(--sky)}
/* hero */
.hero{top:110px;left:0;width:1200px;height:505px;background:linear-gradient(120deg,#4d6d91 0%,#2f4c72 40%,#8aa3bf 75%,#c9d6e3 100%)}
.hero-title{top:188px;width:1200px;text-align:center;color:var(--white);font-size:32px;font-weight:800;line-height:40px;letter-spacing:.5px}
.hero-btn{top:262px;left:551px;width:98px;height:49px;border:1px solid rgba(255,255,255,.8);color:var(--white);font-size:13px;display:flex;align-items:center;justify-content:center}
.hero-arrow{top:240px;width:24px;height:24px;background:rgba(255,255,255,.55);display:flex;align-items:center;justify-content:center}
/* intro */
.intro{top:690px;left:133px;width:934px;text-align:center;font-size:17px;line-height:27px;color:#555}
/* feature band */
.feature-band{top:856px;left:0;width:1200px;height:167px;background:linear-gradient(90deg,var(--violet),var(--soft) 160%);background:linear-gradient(90deg,#6a5cc2 0%,#5a78cc 50%,#4f93d6 100%);color:var(--white);text-align:center;font-size:21px;line-height:32px;padding:36px 180px 0}
/* product section */
.product{top:1023px;left:0;width:1200px;height:681px;background:var(--grey-bg)}
.section-title{width:1200px;text-align:center;color:var(--sky);font-weight:500}
.product-title{top:1098px;font-size:31px;line-height:38px}
.product-lead{top:1190px;left:130px;width:940px;text-align:center;font-size:16px;line-height:25px;color:#555}
.monitor-screen{top:1262px;left:380px;width:440px;height:300px;border-radius:8px;background:linear-gradient(180deg,#2b2b2b,#3a4a5c);border:14px solid #1d1d1d}
.monitor-stand{top:1562px;left:380px;width:440px;height:30px;background:linear-gradient(180deg,#d9d9d9,#bfbfbf);border-radius:0 0 8px 8px}
.monitor-neck{top:1592px;left:560px;width:80px;height:36px;background:linear-gradient(180deg,#c8c8c8,#e4e4e4)}
/* steps */
.steps{top:1704px;left:0;width:1200px;height:278px;background:linear-gradient(90deg,#6a5cc2 0%,#5a78cc 50%,#4f93d6 100%)}
.step{top:1770px;width:200px;text-align:center;color:var(--white);font-size:25px;font-weight:500;line-height:30px}
.step-circle{width:84px;height:84px;border-radius:50%;background:var(--white);margin:0 auto 12px;display:flex;align-items:center;justify-content:center}
.step-op{top:1790px;color:var(--white);font-size:36px;font-weight:400}
/* testimonials */
.testi-title{top:2052px;font-size:31px}
.testi-quote{top:2110px;left:130px;width:940px;text-align:center;font-size:17px;line-height:27px;color:#555}
.testi-author{top:2168px;width:1200px;text-align:center;font-size:13px;color:var(--mid)}
.testi-avatar{top:2198px;left:560px;width:80px;height:80px;border-radius:50%;background:linear-gradient(180deg,#6f6159,#b7a899)}
/* lifecycle */
.lifecycle{top:2360px;left:0;width:1200px;height:645px;background:var(--grey-bg)}
.life-title{top:2428px;left:133px;font-size:31px;font-weight:500;color:var(--sky)}
.card{width:217px;height:198px;background:var(--white);border:1px solid var(--line);padding:26px 20px 0 20px}
.card h3{font-size:17px;font-weight:600;color:var(--navy);margin:12px 0 10px}
.card ul{list-style:disc;padding-left:16px;font-size:11px;line-height:15px;color:#555}
.card li{margin-bottom:6px}
.flow-arrow{width:0;height:0}
/* success */
.success{top:3005px;left:0;width:1200px;height:403px;background:linear-gradient(90deg,#2a2420 0%,#5a4634 35%,#a07a4f 65%,#d2ad7b 100%)}
.success-title{top:3054px;left:669px;width:396px;text-align:center;color:var(--white);font-size:31px}
.success-card{top:3098px;left:669px;width:396px;height:187px;background:rgba(255,255,255,.92);padding:22px 24px;font-size:17px;line-height:27px;color:#555}
.success-author{top:3300px;left:669px;width:396px;text-align:center;color:var(--white);font-size:15px}
.dots{top:3340px;left:827px;display:flex;gap:18px}
.dots span{width:7px;height:7px;border-radius:50%;background:rgba(255,255,255,.6)}
.dots span.on{background:var(--white)}
/* partner / social */
.partner-badge{top:3450px;left:133px;width:157px;height:67px;border:1px solid var(--line);background:#fafafa}
.social{top:3456px;display:flex;gap:26px;left:790px}
.social span{width:52px;height:52px;display:block}
/* footer */
.site-footer{top:3558px;left:0;width:1200px;height:131px;background:var(--foot-bg)}
.foot-links{top:3602px;width:1200px;text-align:center;font-size:12px;color:#555}
.copyright{top:3630px;width:1200px;text-align:center;font-size:11px;color:#666}
</style>
</head>
<body>

<header class="abs site-header">
  <div class="abs brand"><span class="brand-dot"></span><span class="brand-name">Brelvanto</span></div>
  <nav class="abs main-nav">
    <a class="active" href="#">Home</a><a href="#">About</a><a href="#">Partners</a><a href="#">Pricing</a><a href="#">Success Stories</a><a href="#">Testimonials</a><a href="#">Contact us</a>
  </nav>
</header>

<section class="abs hero" role="img" aria-label="Hand touching a glowing network of connected device icons"></section>
<h1 class="abs hero-title">BRIDGING CONNECTED DEVICES<br>WITH ENTERPRISE SOLUTIONS.</h1>
<div class="abs hero-btn">Read more</div>
<div class="abs hero-arrow" style="left:0"><svg width="10" height="10" viewBox="0 0 10 10"><path d="M7 1 3 5l4 4" stroke="#333" stroke-width="1.6" fill="none"/></svg></div>
<div class="abs hero-arrow" style="left:1176px"><svg width="10" height="10" viewBox="0 0 10 10"><path d="M3 1l4 4-4 4" stroke="#333" stroke-width="1.6" fill="none"/></svg></div>

<p class="abs intro">Brelvanto is company which provides specialized offerings in IoT domain. Based in the heart of the Silicon Valley, California. Brelvanto is built on decades of experience and knowledge. Brelvanto CX IoT platform for OEM’s is designed to ease the transition of Product companies from selling unconnected products, into providing service for connected devices.</p>

<div class="abs feature-band">User Management | Device Management | Security | PKI | Billing | Analytics | Vocalia | Murmur | Searchly | Social | Nimbus Cloud | Triggerly | Helpdeskr | chatwise.io | Provisioning | CRM | ERP | Manufacturing | Notifications | Mobile SDK | NOC | Alerts</div>

<section class="abs product"></section>
<h2 class="abs section-title product-title">Focus on your product.<br>We manage the integrations.</h2>
<p class="abs product-lead">With Brelvanto you pick-and-choose the features your customers want, based on our modular architecture. And get all the tools you need to operate your IoT business.</p>
<div class="abs monitor-screen" role="img" aria-label="Dashboard screen showing a map of connected devices and an activity graph"></div>
<div class="abs monitor-stand"></div>
<div class="abs monitor-neck"></div>

<section class="abs steps"></section>
<div class="abs step" style="left:138px"><div class="step-circle"><svg width="34" height="34" viewBox="0 0 24 24"><path d="M5 3h11l3 3v15H5z" fill="#6a6a6a"/><path d="M8 8h8M8 12h8" stroke="#fff" stroke-width="1.5"/></svg></div>Learn</div>
<div class="abs step-op" style="left:345px">+</div>
<div class="abs step" style="left:380px"><div class="step-circle"><svg width="34" height="34" viewBox="0 0 24 24" fill="none" stroke="#6a6a6a" stroke-width="2.4"><circle cx="8" cy="8" r="4"/><circle cx="16" cy="16" r="4"/><path d="M11 11l2 2"/></svg></div>Connect</div>
<div class="abs step-op" style="left:586px">+</div>
<div class="abs step" style="left:618px"><div class="step-circle"><svg width="34" height="34" viewBox="0 0 24 24" fill="#6a6a6a"><circle cx="9" cy="13" r="5"/><circle cx="17" cy="7" r="3.5"/><circle cx="9" cy="13" r="2" fill="#fff"/><circle cx="17" cy="7" r="1.4" fill="#fff"/></svg></div>Integrate</div>
<div class="abs step-op" style="left:826px">=</div>
<div class="abs step" style="left:861px"><div class="step-circle"><svg width="34" height="34" viewBox="0 0 24 24"><circle cx="12" cy="12" r="9" fill="#6a6a6a"/><path d="M7 9c3 0 3 3 6 3s2 5 0 6M14 5c0 3 4 3 5 5" stroke="#fff" stroke-width="1.4" fill="none"/></svg></div>Connected<br>Product</div>

<h2 class="abs section-title testi-title">Testimonials</h2>
<p class="abs testi-quote">“ Phasellus nisl est, condimentum vitae faucibus in, sollicitudin vel metus. Nunc sit amet consequat risus. Curabitur ac elit leo. In eleifend dui tellus, in scelerisque elit porttitor ”</p>
<div class="abs testi-author">- Mara Lind, Company aname</div>
<div class="abs testi-avatar" role="img" aria-label="Portrait of the customer giving the testimonial"></div>

<section class="abs lifecycle"></section>
<h2 class="abs life-title">Brelvanto ensures end-to-end product lifecycle management.</h2>

<article class="abs card" style="left:133px;top:2501px">
  <svg width="40" height="40" viewBox="0 0 24 24" fill="var(--navy)"><circle cx="9" cy="14" r="6"/><circle cx="18" cy="6" r="4"/><circle cx="9" cy="14" r="2.2" fill="#fff"/><circle cx="18" cy="6" r="1.5" fill="#fff"/></svg>
  <h3>Manufacture</h3><ul><li>Secure manufacturing process</li><li>Device traceability in ERP</li></ul></article>
<article class="abs card" style="left:371px;top:2501px">
  <svg width="40" height="40" viewBox="0 0 24 24" fill="var(--navy)"><path d="M3 3h9l9 9-9 9-9-9z"/><circle cx="7.5" cy="7.5" r="1.6" fill="#fff"/></svg>
  <h3>Sell</h3><ul><li>End user tracking in CRM</li><li>Social identity for proactive marketing</li></ul></article>
<article class="abs card" style="left:610px;top:2501px">
  <svg width="40" height="40" viewBox="0 0 24 24" fill="var(--navy)"><path d="M9 3v5M15 3v5" stroke="var(--navy)" stroke-width="2"/><path d="M6 8h12v4a6 6 0 0 1-12 0z"/><path d="M12 18v4" stroke="var(--navy)" stroke-width="2"/></svg>
  <h3>Provision</h3><ul><li>Simplify consumer experience during device activation</li><li>P2P communication via Linkora</li></ul></article>
<article class="abs card" style="left:848px;top:2501px">
  <svg width="40" height="40" viewBox="0 0 24 24" fill="none" stroke="var(--navy)" stroke-width="1.6"><rect x="2" y="6" width="20" height="12" rx="1"/><path d="M5 10h2M9 10h2M13 10h2M17 10h2M7 14h10"/></svg>
  <h3>Use</h3><ul><li>Customer web portal and mobile apps</li><li>Notifications, social identity and advanced IoT services</li></ul></article>
<article class="abs card" style="left:371px;top:2725px">
  <svg width="40" height="40" viewBox="0 0 24 24" fill="none" stroke="var(--navy)" stroke-width="1.8"><rect x="3" y="4" width="18" height="16"/><path d="M7 9h10M7 13h10M7 17h6"/></svg>
  <h3>Maintain</h3><ul><li>Device health check</li><li>Software and security updates</li></ul></article>
<article class="abs card" style="left:610px;top:2725px">
  <svg width="40" height="40" viewBox="0 0 24 24" fill="none" stroke="var(--navy)" stroke-width="2"><path d="M3 3v18h18"/><path d="M6 16l5-5 3 3 6-7"/></svg>
  <h3>Monetize</h3><ul><li>Recurrent user billing</li><li>Additional services and payment options</li></ul></article>
<article class="abs card" style="left:848px;top:2725px">
  <svg width="40" height="40" viewBox="0 0 24 24" fill="none" stroke="var(--navy)" stroke-width="2.2"><path d="M4 15v-3a8 8 0 0 1 16 0v3"/><rect x="3" y="14" width="4" height="6" fill="var(--navy)"/><rect x="17" y="14" width="4" height="6" fill="var(--navy)"/></svg>
  <h3>Support</h3><ul><li>In app chat, ticketing system and call center integration.</li></ul></article>

<svg class="abs" style="left:0;top:0" width="1200" height="3000" aria-hidden="true">
  <path d="M350 2590l12 10-12 10z M589 2590l12 10-12 10z M827 2590l12 10-12 10z" fill="#cfcfcf"/>
  <path d="M946 2700h22l-11 12z" fill="#cfcfcf"/>
  <path d="M847 2815l-12 10 12 10z M609 2815l-12 10 12 10z" fill="#cfcfcf"/>
</svg>

<section class="abs success" role="img" aria-label="Smiling businessman in a suit seated in an orange lounge chair"></section>
<h2 class="abs success-title">Success Stories</h2>
<blockquote class="abs success-card">“ Praesent iaculis faucibus urna sit amet lacinia. Maecenas consequat justo enim, ac mattis massa imperdiet quis. Fusce eget neque elit. Sed augue orci, elemen tum in magna congue. ”</blockquote>
<div class="abs success-author">- Tobias, Company name</div>
<div class="abs dots"><span class="on"></span><span></span><span></span><span></span></div>

<div class="abs partner-badge" role="img" aria-label="Cloud partner network badge"></div>
<div class="abs social" aria-label="Social profiles">
  <span style="background:#3b5998"></span><span style="background:#6b6b6b"></span><span style="background:#7f7f7f"></span><span style="background:#8a8a8a"></span>
</div>

<footer class="abs site-footer"></footer>
<div class="abs foot-links">Home &nbsp;|&nbsp; About &nbsp;|&nbsp; Partners &nbsp;|&nbsp; Pricing &nbsp;|&nbsp; Success Stories &nbsp;|&nbsp; Testimonials &nbsp;|&nbsp; Contact us</div>
<div class="abs copyright">Copyright © 2017 Brelvanto. All rights reserved.</div>

</body>
</html>
```